Pitch Orchard

We need a logo and website that reflects a platform, enabling for users (consultants and corporate clients) to have for them powerpoint slides produced.
See the mockup in attachment - Look& feel Style www.brintova.com. See a similar website content (but outdated presentation and to be made more appealing with new modern ways to promote (old website with same proposition: http://www.yondercraftpanel.com/). Look and feel wished: www.glantirex.com (see number that show dynamic evolution) or www.brintova.com

We have no name - that is part of the mission

```html
<!DOCTYPE html>
<html lang="en">
<head>
<meta charset="utf-8">
<title>Deckwise Visual</title>
<link href="https://fonts.googleapis.com/css2?family=Montserrat:wght@400;600;700&family=Open+Sans:wght@400;600;700&display=swap" rel="stylesheet">
<style>
:root{
  --navy:#0f2a5c;
  --navy-deep:#0a1f47;
  --navy-ring:#13306b;
  --title-blue:#2f4f86;
  --orange:#f07b1d;
  --text:#1b1b1b;
  --muted:#8a8a8a;
  --light:#f5f5f5;
  --band:#f7f7f7;
  --rule:#dfe3ea;
  --white:#ffffff;
  --chart-red:#c8102e;
  --chart-grey:#c9c9c9;
}
*{box-sizing:border-box;margin:0;padding:0}
html,body{width:1200px;height:2449px;overflow:hidden;background:var(--white)}
body{font-family:"Open Sans",Arial,sans-serif;color:var(--text)}
.page{position:relative;width:1200px;height:2449px;overflow:hidden}
.abs{position:absolute}

/* header */
.site-header{left:0;top:0;width:1200px;height:101px;background:linear-gradient(180deg,#1b4589 0%,var(--navy-deep) 100%)}
.brand{left:204px;top:30px;display:flex;align-items:center;gap:10px}
.brand-mark{width:26px;height:26px;border-radius:50%;background:var(--orange)}
.brand-name{font-family:"Montserrat",sans-serif;font-weight:700;font-size:22px;color:var(--white)}
.brand-tag{left:240px;top:60px;font-size:11px;color:#f2a23a;font-family:"Montserrat",sans-serif;font-weight:400}
.main-nav{left:501px;top:42px;display:flex;font-family:"Montserrat",sans-serif;font-weight:600;font-size:11px;color:var(--white)}
.main-nav a{color:inherit;text-decoration:none;position:absolute;white-space:nowrap}
.nav-active::after{content:"";position:absolute;left:0;right:0;top:20px;height:2px;background:#f2c200}
.btn-register{left:898px;top:36px;width:98px;height:29px;background:var(--orange);color:var(--white);font-family:"Montserrat",sans-serif;font-weight:600;font-size:10px;display:flex;align-items:center;justify-content:center;letter-spacing:.3px}

/* hero */
.hero{left:0;top:101px;width:1200px;height:519px;background:linear-gradient(100deg,#e9eef2 0%,#cfd6dc 40%,#8f99a5 70%,#4c5462 100%)}
.hero-title{left:0;top:352px;width:1200px;text-align:center;font-family:"Montserrat",sans-serif;font-weight:700;font-size:39px;color:var(--white);text-shadow:0 2px 6px rgba(0,0,0,.25)}
.hero-btn{left:525px;top:433px;width:150px;height:41px;background:var(--orange);color:var(--white);font-family:"Montserrat",sans-serif;font-weight:600;font-size:12px;display:flex;align-items:center;justify-content:center}
.hero-dots{left:571px;top:571px;display:flex;gap:9px}
.hero-dots span{width:7px;height:7px;border-radius:50%;background:rgba(255,255,255,.55)}
.hero-dots span.on{background:var(--white)}

/* clients */
.clients{left:0;top:620px;width:1200px;height:250px;background:linear-gradient(180deg,#f6f6f6,#f0f0f0)}
.client{width:150px;margin-left:-75px;text-align:center;font-family:"Montserrat",sans-serif;font-weight:700;font-size:16px;color:#7d7d7d}

/* stats */
.stat-ring{width:156px;height:156px;margin-left:-78px;border:4px solid var(--navy-ring);border-radius:50%;display:flex;align-items:center;justify-content:center;font-family:"Open Sans",sans-serif;font-size:34px;color:#9a9a9a;top:943px}
.stat-ring.accent{color:var(--orange)}
.stat-label{width:220px;margin-left:-110px;top:1122px;text-align:center;font-family:"Montserrat",sans-serif;font-weight:700;font-size:16px;line-height:22px;color:var(--navy-deep)}

/* sections */
.band{left:0;top:1241px;width:1200px;height:519px;background:var(--band)}
.section-title{left:0;width:1200px;text-align:center;font-family:"Montserrat",sans-serif;font-weight:600;font-size:25px;color:var(--title-blue)}
.rule{left:199px;width:800px;height:1px;background:var(--rule)}
.sketch{top:1380px;height:260px;border:1px solid #d8d8d8;background:linear-gradient(180deg,#fbfbfb,#efefef)}
.caption{top:1663px;width:390px;text-align:center;font-family:"Montserrat",sans-serif;font-weight:600;font-size:16px}
.arrow{top:1490px;width:16px;height:24px}

/* gallery */
.chart-title{left:576px;top:1894px;width:400px;text-align:center;font-family:"Montserrat",sans-serif;font-weight:600;font-size:13px}
.case-title{left:189px;top:1931px;font-family:"Montserrat",sans-serif;font-weight:700;font-size:22px}
.case-sub{left:189px;top:1964px;font-size:13px;color:var(--muted);font-weight:600}
.case-text{left:189px;top:1996px;width:330px;font-size:11px;line-height:19px;color:#a0a0a0}
.read-more{left:189px;top:2111px;width:115px;height:35px;background:var(--orange);color:var(--white);font-family:"Montserrat",sans-serif;font-weight:600;font-size:11px;display:flex;align-items:center;justify-content:center}
.mini-arrows{left:189px;top:2172px;font-size:16px;color:#c8c8c8;letter-spacing:6px}
.chart-box{left:576px;top:1935px;width:399px;height:261px;border:1px solid #e2e2e2;background:var(--white)}

/* footer */
.footer-rule{left:0;top:2286px;width:1200px;height:1px;background:#e6e6e6}
.social{top:2339px;width:42px;height:42px;margin-left:-21px;border:2px solid #9a9a9a;border-radius:50%;display:flex;align-items:center;justify-content:center;font-family:"Montserrat",sans-serif;font-weight:600;font-size:11px;color:#9a9a9a}
.copyright{left:0;top:2399px;width:1200px;text-align:center;font-size:12px;color:#8a8a8a}
</style>
</head>
<body>
<div class="page">

  <header class="site-header abs">
    <div class="brand abs"><span class="brand-mark"></span><span class="brand-name">Deckwise Visual</span></div>
    <div class="brand-tag abs">adds value to your presentation</div>
    <nav class="main-nav abs">
      <a class="nav-active" style="left:0">Our Value Proposition</a>
      <a style="left:131px">Who Are We</a>
      <a style="left:214px">Pricing</a>
      <a style="left:271px">Free Pilot</a>
      <a style="left:340px">Contact</a>
    </nav>
    <div class="btn-register abs">REGISTRATION</div>
  </header>

  <section class="hero abs" role="img" aria-label="Photo of three business colleagues smiling around a laptop in a bright office"></section>
  <h1 class="hero-title abs">Cost - Speed - Quality</h1>
  <div class="hero-btn abs">LEARN MORE</div>
  <div class="hero-dots abs"><span></span><span class="on"></span><span></span><span></span></div>

  <section class="clients abs" aria-label="Clients">
    <div class="client abs" style="left:253px;top:76px">Kestrel</div>
    <div class="client abs" style="left:430px;top:76px">Halvor</div>
    <div class="client abs" style="left:598px;top:76px">Brunmark</div>
    <div class="client abs" style="left:771px;top:76px">Ostrey Power</div>
    <div class="client abs" style="left:942px;top:76px">Veltrane</div>
    <div class="client abs" style="left:253px;top:158px">Carrowline</div>
    <div class="client abs" style="left:430px;top:158px">Tessmark Systems</div>
    <div class="client abs" style="left:598px;top:158px">Fennick</div>
    <div class="client abs" style="left:771px;top:158px">Lumbrae</div>
    <div class="client abs" style="left:942px;top:158px">Quillby's</div>
  </section>

  <section class="stats" aria-label="Key figures">
    <div class="stat-ring accent abs" style="left:297px">12</div>
    <div class="stat-ring abs" style="left:500px">145</div>
    <div class="stat-ring abs" style="left:702px">20,000</div>
    <div class="stat-ring abs" style="left:906px">1,540</div>
    <div class="stat-label abs" style="left:297px">Candidates</div>
    <div class="stat-label abs" style="left:500px">Coporate Clients<br>Served</div>
    <div class="stat-label abs" style="left:702px">Slides<br>Produced</div>
    <div class="stat-label abs" style="left:906px">Freelance Consultants<br>Served</div>
  </section>

  <section class="band abs"></section>
  <h2 class="section-title abs" style="top:1289px">Animations</h2>
  <div class="rule abs" style="top:1349px"></div>
  <svg class="arrow abs" style="left:92px" viewBox="0 0 16 24"><path d="M12 3 L4 12 L12 21" fill="none" stroke="#9a9a9a" stroke-width="2"/></svg>
  <svg class="arrow abs" style="left:1093px" viewBox="0 0 16 24"><path d="M4 3 L12 12 L4 21" fill="none" stroke="#9a9a9a" stroke-width="2"/></svg>
  <div class="sketch abs" style="left:199px;width:392px" role="img" aria-label="Hand-drawn sketch of a slide storyboard before redesign"></div>
  <div class="sketch abs" style="left:609px;width:389px" role="img" aria-label="Hand-drawn sketch of a slide storyboard after redesign"></div>
  <div class="caption abs" style="left:194px">Before</div>
  <div class="caption abs" style="left:604px">After</div>

  <h2 class="section-title abs" style="top:1818px">Gallery</h2>
  <div class="rule abs" style="top:1873px"></div>
  <div class="chart-title abs">Illustrative Cost Structure Of A Carve-Out,$ Millions</div>
  <h3 class="case-title abs">Private Equity Industry</h3>
  <div class="case-sub abs">Operational Value Ctreation/ Quest In Carve Outs</div>
  <p class="case-text abs">Sed ut perspiciatis unde omnis iste natus error sit voluptatem accusantium doloremque laudantium, totam rem aperiam, eaque ipsa quae ab illo inventore veritatis et quasi architecto beatae vitae dicta sunt explicabo. Nemo enim ipsam voluptatem quia voluptas sit aspernatur aut odit aut fugit.</p>
  <div class="read-more abs">Read More</div>
  <div class="mini-arrows abs">‹ ›</div>

  <div class="chart-box abs">
    <svg width="399" height="261" viewBox="0 0 399 261" font-family="Open Sans, sans-serif" font-size="5" fill="#333">
      <rect x="310" y="12" width="10" height="10" fill="var(--chart-red)"/>
      <text x="324" y="21" font-size="9" font-weight="700">Norvak</text>
      <text x="150" y="40">Run rate savings total one-time costs</text>
      <line x1="70" y1="44" x2="370" y2="44" stroke="#c8102e" stroke-width=".6"/>
      <line x1="20" y1="160" x2="385" y2="160" stroke="#888" stroke-width=".6"/>
      <!-- bars -->
      <rect x="26" y="70" width="22" height="90" fill="var(--chart-grey)" stroke="#777" stroke-width=".5"/>
      <text x="28" y="66">$2,145</text>
      <rect x="62" y="70" width="22" height="3" fill="#999"/>
      <rect x="96" y="73" width="22" height="87" fill="var(--chart-grey)" stroke="#777" stroke-width=".5"/>
      <rect x="96" y="140" width="22" height="20" fill="var(--chart-red)"/>
      <text x="98" y="69">$2,131</text>
      <rect x="130" y="73" width="22" height="8" fill="var(--chart-red)"/>
      <rect x="164" y="81" width="22" height="3" fill="#999"/>
      <rect x="198" y="84" width="22" height="3" fill="var(--chart-red)"/>
      <rect x="232" y="87" width="22" height="3" fill="#999"/>
      <rect x="266" y="90" width="22" height="3" fill="var(--chart-red)"/>
      <rect x="300" y="93" width="22" height="67" fill="var(--chart-grey)" stroke="#777" stroke-width=".5"/>
      <rect x="300" y="140" width="22" height="20" fill="var(--chart-red)"/>
      <text x="301" y="89">$1,902</text>
      <text x="22" y="170">Current base</text>
      <text x="60" y="170">Savings</text>
      <text x="92" y="170">Standalone</text>
      <text x="128" y="170">Headcount</text>
      <text x="162" y="170">Non-staff</text>
      <text x="196" y="170">Footprint</text>
      <text x="232" y="170">Material</text>
      <text x="296" y="170">New base</text>
      <rect x="12" y="182" width="375" height="44" fill="none" stroke="#c8102e" stroke-width=".8"/>
      <text x="16" y="192">Illustrative example of the cost structure of a carve-out involves understanding:</text>
      <text x="16" y="201">Standalone impact, which includes added costs to replace shared services</text>
      <text x="16" y="210">Performance improvement opportunities, which must focus on value creation</text>
      <text x="16" y="219">Timing and sequence of activities are defined as part of the operating plan</text>
      <text x="12" y="236">Source: analysis</text>
    </svg>
  </div>

  <div class="footer-rule abs"></div>
  <footer>
    <div class="social abs" style="left:511px">Kv</div>
    <div class="social abs" style="left:570px">Rp</div>
    <div class="social abs" style="left:629px">Ql</div>
    <div class="social abs" style="left:687px">Mz</div>
    <div class="copyright abs">© 2016 Company Name &nbsp;|&nbsp; All Rights Reserved</div>
  </footer>

</div>
</body>
</html>
```